Property management company looking for modern card design

We at Blue Heron Partners provides property management services for its residential and commercial properties, with expertise in all categories of multifamily, industrial and office projects throughout California.

We need a business card design that is professional and modern designed business card. In our field, clients get hundreds of business cards, we would like our card to stand out.

Please avoid small print.

Target Market(s)

Professionals and high end clients

Industry/Entity Type

Financial Planning

Contact Information for Business Card

Company Name: Blue Heron Partners, Name, email, license #, phone number, website blueheronpartners.com

Font styles to use
Sans Serif

Requirements
Must have
• The card design needs to be adaptable because there is a possibly we will be expanding into different sectors other than real estate. The card design should be focused on financial planning and asset management.
Nice to have
• Modern and simple business card. Eye catching. Non-standard size/shaped cards would be great.
• blueheronpartners.com
Should not have
• Too many bright color or any pictures or shapes of real estate stuff.

```html
<!DOCTYPE html>
<html lang="en">
<head>
<meta charset="utf-8">
<title>Blue Heron Partners – Business Card</title>
<link href="https://fonts.googleapis.com/css2?family=Arimo:wght@400&display=swap" rel="stylesheet">
<style>
  :root {
    --backdrop: #8f8f90;
    --kraft: #a8875a;
    --kraft-edge: #9a7a4e;
    --accent: #e21f3d;
    --ink: #1f1a14;
  }
  * { margin: 0; padding: 0; box-sizing: border-box; }
  html, body {
    width: 1200px; height: 902px; overflow: hidden;
    background: var(--backdrop);
    font-family: "Arimo", Arial, sans-serif;
  }
  .stage {
    width: 1200px; height: 902px;
    display: flex; align-items: center; justify-content: center;
  }
  .card {
    position: relative;
    width: 1000px; height: 572px;
    background: var(--kraft);
    border: 1px solid var(--kraft-edge);
    box-shadow: 0 8px 24px rgba(0,0,0,0.25);
  }
  .brand-mark {
    position: absolute; left: 215px; top: 120px;
    width: 180px; height: 180px; border-radius: 50%;
    background: var(--accent);
  }
  .brand-name {
    position: absolute; left: 90px; top: 350px; width: 440px;
    text-align: center;
    color: var(--accent);
    font-size: 40px; letter-spacing: 8px;
    text-transform: uppercase;
  }
  .divider {
    position: absolute; left: 560px; top: 80px;
    width: 3px; height: 410px; background: var(--accent);
  }
  .holder-name {
    position: absolute; left: 610px; top: 110px;
    color: var(--accent); font-size: 34px;
  }
  .contact-list {
    position: absolute; left: 610px; top: 230px;
    list-style: none;
  }
  .contact-list li {
    display: flex; align-items: center; gap: 14px;
    height: 50px;
    color: var(--ink); font-size: 27px;
  }
  .contact-icon {
    width: 26px; height: 26px; flex: none;
  }
  .license {
    position: absolute; left: 610px; top: 400px;
    color: var(--ink); font-size: 30px;
  }
</style>
</head>
<body>
<main class="stage">
  <section class="card">
    <div class="brand-mark"></div>
    <div class="brand-name">Blue Heron</div>
    <div class="divider"></div>
    <div class="holder-name">Alex Moreno</div>
    <ul class="contact-list">
      <li>
        <svg class="contact-icon" viewBox="0 0 26 26" aria-hidden="true">
          <rect width="26" height="26" fill="var(--accent)"/>
          <path d="M8 6 l3 0 l1 4 l-2 1.5 q1.5 3 4.5 4.5 l1.5 -2 l4 1 l0 3 q-8 1 -12 -12z" fill="var(--ink)"/>
        </svg>
        <span>555-014-2291</span>
      </li>
      <li>
        <svg class="contact-icon" viewBox="0 0 26 26" aria-hidden="true">
          <rect width="26" height="26" fill="var(--accent)"/>
          <rect x="5" y="8" width="16" height="11" fill="none" stroke="var(--ink)" stroke-width="1.8"/>
          <path d="M5 8 l8 6 l8 -6" fill="none" stroke="var(--ink)" stroke-width="1.8"/>
        </svg>
        <span>info@blueheron.com</span>
      </li>
      <li>
        <svg class="contact-icon" viewBox="0 0 26 26" aria-hidden="true">
          <rect width="26" height="26" fill="var(--accent)"/>
          <circle cx="13" cy="13" r="8" fill="none" stroke="var(--ink)" stroke-width="1.6"/>
          <ellipse cx="13" cy="13" rx="3.5" ry="8" fill="none" stroke="var(--ink)" stroke-width="1.4"/>
          <path d="M5 13 h16" stroke="var(--ink)" stroke-width="1.4"/>
        </svg>
        <span>blueheronpartners.com</span>
      </li>
    </ul>
    <div class="license">Lic : 20480135</div>
  </section>
</main>
</body>
</html>
```